Computer consultant business card

Bexil Software is a newly started computer consulting company. It's a small one-man company that provides mostly Vornix applications but also websites in collaboration with designers. I'm running this company on the side of full time university studies.

I want the final design to be clean and memorable. Be creative! :)

Some inspiration:
http://www.pixelmarta.com/design/48317
http://www.pixelmarta.com/design/2739164/business-card-design-by-frostlynk
http://www.pixelmarta.com/design/604281/business-card-design-by-koralind-vestrabanu

See attachment for my company logo.
Updates

I would like to thank everyone for submitting! I'll need a couple of days to review and ultimately select a design.

Target Market(s)

Non-technical entrepreneurs and small companies.

Industry/Entity Type

University

Requirements
Must have
• My company logo.
In any way, both colors from my logo.
First- and last name, e-mail and phone number.
Double-sided design.
Nice to have
• Something creative with the symbol in my logo

```html
<!DOCTYPE html>
<html lang="en">
<head>
<meta charset="utf-8">
<title>Tovrel – Business Card</title>
<link rel="stylesheet" href="https://fonts.googleapis.com/css2?family=Jost:wght@400;500;600&display=swap">
<style>
  :root {
    --stage: #e8e5e0;
    --ink: #333236;
    --brand-blue: #4a72b8;
    --band: #333236;
    --white: #ffffff;
    --label: #1e1e1e;
    --night: #050505;
    --slate-dark: #34363d;
    --slate-blue: #4d5b80;
  }
  * { box-sizing: border-box; margin: 0; padding: 0; }
  html, body { width: 1200px; height: 788px; overflow: hidden; }
  body {
    position: relative;
    background: var(--stage);
    font-family: "Jost", "Century Gothic", sans-serif;
  }
  .side-label {
    position: absolute;
    width: 526px;
    text-align: center;
    font-family: Arial, Helvetica, sans-serif;
    font-size: 20px;
    color: var(--label);
  }
  .card {
    position: absolute;
    width: 526px;
    height: 299px;
    border-radius: 18px;
    overflow: hidden;
    box-shadow: 0 4px 10px rgba(0,0,0,0.25);
  }
  .card--front, .card--back-light { background: var(--white); }
  .card--back-dark { background: var(--night); }
  .card--back-slate {
    background: radial-gradient(ellipse at 70% 95%, var(--slate-blue) 0%, #404862 50%, var(--slate-dark) 100%);
  }
  .wordmark {
    position: absolute;
    display: flex;
    align-items: center;
    gap: 20px;
    left: 50%;
    transform: translateX(-50%);
    white-space: nowrap;
  }
  .wordmark__dot {
    border-radius: 50%;
    background: var(--brand-blue);
    flex: none;
  }
  .wordmark__name {
    font-weight: 500;
    line-height: 1;
    color: var(--ink);
  }
  .wordmark--small { top: 52px; }
  .wordmark--small .wordmark__dot { width: 74px; height: 74px; }
  .wordmark--small .wordmark__name { font-size: 64px; }
  .wordmark--large { top: 88px; }
  .wordmark--large .wordmark__dot { width: 96px; height: 96px; }
  .wordmark--large .wordmark__name { font-size: 82px; }
  .wordmark--reversed .wordmark__name { color: var(--white); }

  .contact-band {
    position: absolute;
    left: 0; right: 0;
    top: 183px;
    height: 76px;
    border-top: 2px solid var(--brand-blue);
    border-bottom: 2px solid var(--brand-blue);
    background: var(--white);
    padding: 3px 0;
  }
  .contact-band__inner {
    height: 100%;
    background: var(--band);
    color: var(--white);
    display: flex;
    justify-content: space-between;
    align-items: center;
    padding: 0 32px;
  }
  .person__name { font-size: 18px; font-weight: 600; letter-spacing: 0.3px; }
  .person__role { font-size: 13px; margin-top: 1px; }
  .contact { text-align: right; font-size: 15px; line-height: 20px; }
  .contact__key { font-weight: 600; font-style: italic; }

  .website {
    position: absolute;
    left: 0; right: 0;
    bottom: 26px;
    text-align: center;
    font-size: 18px;
    letter-spacing: 3.5px;
    color: var(--ink);
  }
  .website--reversed { color: var(--white); }

  .texture {
    position: absolute;
  }
  .texture--top {
    left: -40px; top: -110px; width: 360px; height: 240px;
    background: radial-gradient(ellipse closest-side at 55% 55%, rgba(110,110,110,0.5) 0%, rgba(40,40,40,0.3) 50%, rgba(5,5,5,0) 100%);
  }
  .texture--bottom {
    right: -60px; bottom: -100px; width: 300px; height: 260px;
    background: radial-gradient(ellipse closest-side at 45% 45%, rgba(140,130,130,0.5) 0%, rgba(50,45,45,0.3) 50%, rgba(5,5,5,0) 100%);
  }
</style>
</head>
<body>
  <div class="side-label" style="left:54px; top:35px;">Front</div>
  <div class="side-label" style="left:622px; top:35px;">Back - 1</div>
  <div class="side-label" style="left:54px; top:405px;">Back - 2</div>
  <div class="side-label" style="left:622px; top:405px;">Back - 3</div>

  <section class="card card--front" style="left:54px; top:75px;">
    <div class="wordmark wordmark--small">
      <span class="wordmark__dot"></span>
      <span class="wordmark__name">tovrel</span>
    </div>
    <div class="contact-band">
      <div class="contact-band__inner">
        <div class="person">
          <div class="person__name">First Name + Last Name</div>
          <div class="person__role">Designation</div>
        </div>
        <div class="contact">
          <div><span class="contact__key">Phone</span> : +12 345 6789</div>
          <div><span class="contact__key">email</span> : info@website.com</div>
        </div>
      </div>
    </div>
  </section>

  <section class="card card--back-light" style="left:622px; top:75px;">
    <div class="wordmark wordmark--large">
      <span class="wordmark__dot"></span>
      <span class="wordmark__name">tovrel</span>
    </div>
    <div class="website">www.website.com</div>
  </section>

  <section class="card card--back-dark" style="left:54px; top:446px;">
    <div class="texture texture--top" role="img" aria-label="Perforated metal dot texture"></div>
    <div class="texture texture--bottom" role="img" aria-label="Perforated metal dot texture"></div>
    <div class="wordmark wordmark--large wordmark--reversed">
      <span class="wordmark__dot"></span>
      <span class="wordmark__name">tovrel</span>
    </div>
    <div class="website website--reversed">www.website.com</div>
  </section>

  <section class="card card--back-slate" style="left:622px; top:446px;">
    <div class="wordmark wordmark--large wordmark--reversed">
      <span class="wordmark__dot"></span>
      <span class="wordmark__name">tovrel</span>
    </div>
    <div class="website website--reversed">www.website.com</div>
  </section>
</body>
</html>
```